Harbourline Electrical Solutions

On one side. LOGO (underneath:) Commercial Industrial Residential

- NAME & CONTACT DETAILS

Marcus T. Hollings
Project Manager

(Cell icon) (441) 555-0187
(Email icon) hlelectricalsolutions@mailvento.com
(Facebook & Instagram icons )@hlelectricalsolutions

Other side: LOGO - underneath ELECTRICAL CONSTRUCTION & MAINTENANCE . LED LIGHTING & AUTOMATION . LIFE SAFETY SYSTEMS (FIRE ALARM / SECURITY) . DATA & COMMUNICATION

```html
<!DOCTYPE html>
<html lang="en">
<head>
<meta charset="utf-8">
<title>Harbourline Electrical Solutions – Business Card</title>
<link href="https://fonts.googleapis.com/css2?family=Montserrat:wght@400;500;600;700&display=swap" rel="stylesheet">
<style>
  :root{
    --teal:#0f5a6e;
    --teal-text:#12596d;
    --white:#ffffff;
    --ink:#3a3a3a;
    --rule:#555555;
    --backdrop:#e9ebec;
  }
  *{box-sizing:border-box;margin:0;padding:0}
  html,body{width:1200px;height:1200px;overflow:hidden}
  body{
    background:var(--backdrop);
    font-family:"Montserrat",Arial,sans-serif;
    position:relative;
  }
  .card{
    position:absolute;
    left:220px;
    width:760px;
    height:434px;
    box-shadow:0 10px 30px rgba(0,0,0,.18);
  }
  /* back side */
  .card--back{
    top:150px;
    background:var(--teal);
    color:var(--white);
    border-radius:90px 0 90px 0;
  }
  .card--back .brand{
    position:absolute;
    top:120px;left:0;right:0;
    display:flex;justify-content:center;align-items:center;gap:18px;
  }
  .brand__mark{width:34px;height:34px;flex:none}
  .card--back .brand__mark{background:var(--white)}
  .brand__name{
    font-weight:600;
    letter-spacing:.12em;
    text-transform:uppercase;
    line-height:1.15;
  }
  .card--back .brand__name{font-size:24px;color:var(--white)}
  .services{
    position:absolute;
    top:265px;left:0;right:0;
    text-align:center;
    font-size:15px;
    font-weight:500;
    letter-spacing:.06em;
    line-height:1.45;
    text-transform:uppercase;
  }
  /* front side */
  .card--front{
    top:616px;
    background:var(--white);
    border-radius:0 90px 0 90px;
  }
  .card--front .brand{
    position:absolute;
    top:46px;left:54px;
    display:flex;align-items:center;gap:14px;
  }
  .card--front .brand__mark{background:var(--teal)}
  .card--front .brand__name{font-size:22px;color:var(--teal-text)}
  .tagline{
    position:absolute;
    top:104px;left:54px;
    font-size:15px;
    color:var(--ink);
    letter-spacing:.05em;
    text-transform:uppercase;
  }
  .contact{
    position:absolute;
    top:178px;left:300px;
    padding-left:22px;
    border-left:2px solid var(--rule);
    color:var(--ink);
  }
  .contact__name{
    font-size:24px;font-weight:700;
    color:var(--teal-text);
    text-transform:uppercase;
    letter-spacing:.02em;
  }
  .contact__role{font-size:17px;margin-bottom:14px}
  .contact__row{
    display:flex;align-items:center;gap:8px;
    font-size:18px;line-height:1.5;
  }
  .contact__row svg{flex:none}
  .social{display:flex;gap:8px;margin-top:12px}
  .social__dot{
    width:26px;height:26px;border-radius:50%;
    border:2px solid var(--teal);
  }
  .contact__handle{font-size:18px;margin-top:4px}
</style>
</head>
<body>

  <section class="card card--back" aria-label="Card back">
    <div class="brand">
      <span class="brand__mark"></span>
      <span class="brand__name">Harbourline<br>Electrical<br>Solutions</span>
    </div>
    <p class="services">
      Electrical Construction &amp; Maintenance<br>
      LED Lighting &amp; Automation | Data &amp; Communication<br>
      Life Safety Systems (Fire Alarm / Security)
    </p>
  </section>

  <section class="card card--front" aria-label="Card front">
    <div class="brand">
      <span class="brand__mark"></span>
      <span class="brand__name">Harbourline Electrical Solutions</span>
    </div>
    <p class="tagline">Commercial Industrial Residential</p>

    <div class="contact">
      <p class="contact__name">Marcus T. Hollings</p>
      <p class="contact__role">Project Manager</p>
      <p class="contact__row">
        <svg width="14" height="20" viewBox="0 0 14 20" aria-hidden="true">
          <rect x="1" y="1" width="12" height="18" rx="2" fill="none" stroke="var(--teal)" stroke-width="2"/>
          <line x1="5" y1="15.5" x2="9" y2="15.5" stroke="var(--teal)" stroke-width="1.6"/>
        </svg>
        (441) 555-0187
      </p>
      <p class="contact__row">
        <svg width="18" height="13" viewBox="0 0 18 13" aria-hidden="true">
          <rect x="0" y="0" width="18" height="13" rx="1" fill="var(--teal)"/>
          <polyline points="1,1 9,7.5 17,1" fill="none" stroke="var(--white)" stroke-width="1.5"/>
        </svg>
        hlelectricalsolutions@mailvento.com
      </p>
      <div class="social" aria-label="Social profiles">
        <span class="social__dot"></span>
        <span class="social__dot"></span>
      </div>
      <p class="contact__handle">@hlelectricalsolutions</p>
    </div>
  </section>

</body>
</html>
```